Stationary design for boutique production house

We need a stationary design for our production house, 'Lorno Productions' based in Singapore. We produce microfilms as well as podcasts, talkshows and events. Our logo is a stylized icon of our director, who is also the executive producer and host of our programs, Lorno. Our main company colors are Red, Black and white. We would like a clean, minimalist design incorporating our existing company logo that conveys a sense of urbanism and elegance.

Logo and font files are attached. f

Target Market(s)

We focus on lifestyle media rather than entertainment.

Industry/Entity Type

Boutique

Font styles to use
Serif
Sans Serif

Colors
ec1f27
ffffff
000000

Requirements
Must have
• Our company logo and at least one of our company colors.
Nice to have
• Our address and contact information.
Should not have
• Changes made to the company logo (using only certain parts of it is fine though)

```html
<!DOCTYPE html>
<html lang="en">
<head>
<meta charset="utf-8">
<title>Lorno Productions — Stationery</title>
<link href="https://fonts.googleapis.com/css2?family=Libre+Baskerville&family=Open+Sans:wght@400;600&display=swap" rel="stylesheet">
<style>
  :root {
    --red: #ec1f27;
    --deep-red: #a10f16;
    --black: #111111;
    --band: #1c1c1c;
    --paper: #ececec;
    --white: #ffffff;
    --backdrop: #e4dccb;
    --serif: "Libre Baskerville", "Times New Roman", serif;
    --sans: "Open Sans", Arial, sans-serif;
  }
  * { box-sizing: border-box; margin: 0; padding: 0; }
  html, body { width: 1200px; height: 1118px; overflow: hidden; }
  body { background: var(--backdrop); position: relative; font-family: var(--sans); }

  .brand-name {
    font-family: var(--serif);
    font-weight: 400;
    color: var(--black);
    display: flex;
    align-items: center;
    gap: 10px;
    letter-spacing: 0.02em;
    white-space: nowrap;
  }
  .brand-dot { display: inline-block; border-radius: 50%; background: var(--red); flex: none; }

  /* Letterhead */
  .letterhead {
    position: absolute; left: 570px; top: 150px; width: 560px; height: 800px;
    background: var(--paper);
    box-shadow: 0 3px 10px rgba(0,0,0,0.18);
  }
  .letterhead-header {
    height: 112px; background: var(--band);
    border-bottom: 4px solid var(--red);
    display: flex; justify-content: space-between; align-items: flex-start;
    padding: 28px 34px 0 34px;
  }
  .letterhead-header .brand-name { color: var(--white); font-size: 17px; margin-top: 8px; }
  .letterhead-address { color: var(--white); font-family: var(--serif); font-size: 11px; line-height: 1.5; }
  .letterhead-address .phone { font-family: var(--sans); font-size: 10.5px; display: block; margin-top: 3px; }

  /* Envelope */
  .envelope {
    position: absolute; left: 60px; top: 250px; width: 470px; height: 250px;
    background: var(--paper); overflow: hidden;
    box-shadow: 0 3px 10px rgba(0,0,0,0.18);
  }
  .envelope-flap-line {
    position: absolute; left: 0; top: 58px; width: 100%; height: 5px;
    background: var(--deep-red);
  }
  .envelope .brand-name { position: absolute; left: 40px; top: 120px; font-size: 20px; }
  .envelope-band {
    position: absolute; left: 0; bottom: 0; width: 100%; height: 52px;
    background: var(--band); border-top: 4px solid var(--red);
    color: var(--white); font-family: var(--serif); font-size: 12px;
    display: flex; align-items: center; padding-left: 40px;
  }

  /* Business cards */
  .card {
    position: absolute; width: 280px; height: 160px; overflow: hidden;
    background: var(--paper);
    box-shadow: 0 3px 8px rgba(0,0,0,0.2);
  }
  .card-back { left: 150px; top: 580px; }
  .card-front { left: 150px; top: 780px; display: flex; align-items: center; justify-content: center; }
  .card-back svg { position: absolute; left: 0; top: 0; }
  .card-back .brand-name { position: absolute; left: 0; width: 100%; top: 30px; justify-content: center; font-size: 14px; }
  .card-contacts {
    position: absolute; left: 0; width: 100%; top: 100px;
    color: var(--white); font-size: 8.5px; text-align: center; line-height: 1.6;
  }
  .card-contacts .row { display: flex; justify-content: center; gap: 14px; align-items: center; }
  .card-contacts .item { display: inline-flex; align-items: center; gap: 4px; }
  .card-front .brand-name { font-size: 17px; }
</style>
</head>
<body>

  <section class="letterhead" aria-label="Letterhead">
    <header class="letterhead-header">
      <div class="brand-name"><span class="brand-dot" style="width:9px;height:9px"></span>Lorno Productions</div>
      <p class="letterhead-address">
        18 Kallang Way,<br>
        Meridian Works Building,<br>
        #03 12, Singapore 349210
        <span class="phone">+65 6410 5872</span>
      </p>
    </header>
  </section>

  <section class="envelope" aria-label="Envelope">
    <div class="envelope-flap-line"></div>
    <div class="brand-name"><span class="brand-dot" style="width:10px;height:10px"></span>Lorno Productions</div>
    <div class="envelope-band">18 Kallang Way, Meridian Works Building, #03 12, Singapore 349210</div>
  </section>

  <section class="card card-back" aria-label="Business card, back">
    <svg width="280" height="160" viewBox="0 0 280 160" aria-hidden="true">
      <path d="M0 72 Q140 120 280 72 L280 160 L0 160 Z" fill="var(--deep-red)"/>
      <rect x="0" y="150" width="280" height="10" fill="var(--black)"/>
    </svg>
    <div class="brand-name"><span class="brand-dot" style="width:7px;height:7px"></span>Lorno Productions</div>
    <div class="card-contacts">
      <div class="row">
        <span class="item">
          <svg width="9" height="9" viewBox="0 0 24 24" aria-hidden="true"><path fill="#fff" d="M6.6 10.8a15 15 0 006.6 6.6l2.2-2.2c.3-.3.7-.4 1-.2 1.1.4 2.3.6 3.6.6.6 0 1 .4 1 1V20c0 .6-.4 1-1 1A17 17 0 013 4c0-.6.4-1 1-1h3.5c.6 0 1 .4 1 1 0 1.3.2 2.5.6 3.6.1.3 0 .7-.2 1z"/></svg>
          +65 6410 5872
        </span>
        <span class="item">
          <svg width="10" height="8" viewBox="0 0 20 16" aria-hidden="true"><rect x="1" y="1" width="18" height="14" fill="none" stroke="#fff" stroke-width="2"/><path d="M1 1l9 7 9-7" fill="none" stroke="#fff" stroke-width="2"/></svg>
          hello@lornoproductions.sg
        </span>
      </div>
      <div>18 Kallang Way, Meridian Works Building, #03 12,</div>
      <div>Singapore 349210</div>
    </div>
  </section>

  <section class="card card-front" aria-label="Business card, front">
    <div class="brand-name"><span class="brand-dot" style="width:9px;height:9px"></span>Lorno Productions</div>
  </section>

</body>
</html>
```